Music Producer Website

I need a website designed for my music production company. We specialize in finding talented musicians and matching them with music producers all over the United States. A visitor can create a profile and/or upload their music demo and we submit it to thousands of music producers and production companies for review. In many cases, our members will receive multiple signing offers from music producers allowing them to choose the contract that is best for them. "We turn aspiring musicians into SuperStars!"
Please include photos that reflect all genres of music (black artists, white artists, both male and female.) We produce all types of music including rap, R&B, rock, country, and Hip Hop.
When a user creates a profile, they become visible to thousands of record producers who are looking to sign new talent and make them stars.
Somewhere in the top half of the page, please include a small form that the visitor can fill out. The form should look as follows:
Title (large and bold): Contact Us or Submit Music Demo
Fields to include (* = required): First Name*, Last Name*, Age, Zip Code, Email Address*, Daytime Phone, Evening Phone, Comments
Then, there will be a "submit" button to proceed to next step of form. Just below the "submit" button, should be the following verbiage: "After submitting, you will have the opportunity to upload demos of your music (optional) and provide other pertinent information about yourself, band, or group."
Updates
Reason: I have not seen a design that I am 100% satisfied with yet. Ideally, rotating header images (GIF or other) with several different music producers in studio (male, female, black, white) would be perfect. Here are some examples of how the header pics could look:
http://files.quillmarsh.net/art_img/514302/806421/806421_7391046_514302_image.jpg
http://files.quillmarsh.net/art_img/514302/806421/806421_7391058_514302_image.jpg
http://files.quillmarsh.net/art_img/514302/806421/806421_7391037_514302_image.jpg
Also, there should be a form on the site (somewhere in upper half of the page) with the following headline:
GET FOUND AND BECOME A STAR! (super large, super-bold font)
Contact Us or Submit Your Music for Review (large font, not as bold as headline)
First Name
Last Name
Age
Zip Code
Email Address
Daytime Phone
Evening Phone
Comments
Target Market(s)
We are targeting all types of musicians including rock, rap, pop, R&B, country, gospel, etc.
Industry/Entity Type
Artists
Colors
Designer to choose colors to be used in the design.
Look and feel
Each slider illustrates characteristics of the customer's brand and the style your logo design should communicate.

```html
<!DOCTYPE html>
<html lang="en">
<head>
<meta charset="utf-8">
<title>Vantage Music Productions</title>
<link href="https://fonts.googleapis.com/css2?family=Cinzel:wght@400;700&family=Ubuntu:wght@400;500;700&display=swap" rel="stylesheet">
<style>
:root{
  --black:#000;
  --gold:#c8a75a;
  --gold-deep:#a8893f;
  --gold-light:#e2c77f;
  --field:#6b5517;
  --field-text:#d8bd72;
  --text-muted:#9d8a5c;
  --text-soft:#c9c3b3;
  --review-text:#a99e84;
  --footer-text:#2a1f08;
}
*{box-sizing:border-box;margin:0;padding:0}
html,body{width:793px;height:1200px;overflow:hidden;background:var(--black)}
body{font-family:"Ubuntu",sans-serif;color:var(--text-soft);position:relative}
.abs{position:absolute}
h2,h3{font-weight:400}

/* header */
.site-header{left:0;top:0;width:793px;height:78px;background:var(--black)}
.brand{left:58px;top:0;width:164px;height:78px;background:#111;display:flex;flex-direction:column;align-items:center;justify-content:center}
.brand-name{font-family:"Cinzel",serif;color:var(--gold);font-size:22px;letter-spacing:1px;line-height:1}
.brand-sub{font-family:"Cinzel",serif;color:var(--gold);font-size:7.5px;letter-spacing:2px;margin-top:4px}
.main-nav a{position:absolute;top:45px;font-family:"Cinzel",serif;font-size:10px;color:var(--gold);text-decoration:none;letter-spacing:.3px}
.nav-note{left:324px;top:28px}
.account-btn{top:14px;height:16px;font-family:"Cinzel",serif;font-size:8px;display:flex;align-items:center;justify-content:center;color:#222}
.account-btn.signup{left:597px;width:54px;background:linear-gradient(#fff,#bbb)}
.account-btn.login{left:654px;width:51px;background:linear-gradient(#f2dc8e,#c49a33)}

/* hero */
.hero{left:0;top:78px;width:793px;height:333px;
  background:
    radial-gradient(ellipse 60px 40px at 295px 60px,rgba(230,225,215,.55),transparent 70%),
    radial-gradient(ellipse 60px 40px at 415px 55px,rgba(230,225,215,.55),transparent 70%),
    linear-gradient(160deg,transparent 38%,rgba(120,120,125,.55) 44%,rgba(70,70,74,.7) 60%,rgba(30,30,32,.8) 80%,transparent 92%),
    radial-gradient(ellipse at 20% 25%,#8a6a48 0%,#5a4230 30%,transparent 65%),
    radial-gradient(ellipse at 95% 60%,#5a4226 0%,transparent 55%),
    linear-gradient(180deg,#2a1d14 0%,#4a3626 45%,#1a120c 100%)}
.hero-tagline{left:108px;top:228px;font-family:"Cinzel",serif;font-size:12px;color:#fff;letter-spacing:.3px}
.form-title{left:520px;top:103px;font-family:"Cinzel",serif;font-size:10px;color:var(--gold-light);letter-spacing:.4px}
.demo-form{left:522px;top:121px;width:185px;height:257px;background:var(--gold-deep)}
.field{position:absolute;left:11px;width:162px;height:22px;background:var(--field);color:var(--field-text);font-size:7.5px;padding:0 7px;display:flex;align-items:center}
.field.comments{align-items:flex-start;padding-top:6px;height:52px}
.submit-btn{position:absolute;left:55px;top:227px;width:75px;height:20px;background:linear-gradient(#e3b84a,#9b7418);color:#fff;font-size:8px;font-weight:700;display:flex;align-items:center;justify-content:center;border-radius:2px}
.slider-track{left:79px;top:389px;width:627px;height:10px;border-radius:5px;background:linear-gradient(#c9a757,#8a6b25)}
.slider-thumb{left:81px;top:391px;width:40px;height:6px;border-radius:3px;background:#3b321d}

/* partners */
.partners{left:0;top:411px;width:793px;height:56px;background:var(--gold);display:flex;align-items:center;justify-content:space-around;padding:0 90px}
.partner{font-weight:700;font-size:16px;color:#111}

/* section headings */
.section-title{font-family:"Cinzel",serif;font-size:10.5px;color:var(--gold);letter-spacing:.6px}
.arrow-btn{top:483px;width:16px;height:14px;background:var(--gold);display:flex;align-items:center;justify-content:center}

/* demo grid */
.demo-card{width:108px}
.thumb{width:108px;height:82px;border:1px solid #8a7a55;position:relative;display:flex;align-items:center;justify-content:center;background-blend-mode:normal}
.play{width:26px;height:26px}
.caption{font-size:7.5px;color:var(--text-muted);line-height:14px;margin-top:6px}

.pager{left:191px;top:1104px;display:flex;gap:5px}
.page{height:16px;min-width:16px;padding:0 4px;background:var(--gold);color:#fff;font-size:7.5px;display:flex;align-items:center;justify-content:center}
.page.wide{width:32px}

/* right column */
.track{left:475px;width:240px}
.track .thumb{width:67px;height:60px;position:absolute;left:0;top:0}
.track-title{position:absolute;left:76px;top:10px;font-size:9px;color:var(--gold-light);white-space:nowrap}
.track-text{position:absolute;left:76px;top:28px;width:160px;font-size:7.5px;color:#ddd;line-height:13px}
.read-more{width:57px;height:19px;background:var(--gold);color:#2a1d06;font-family:"Cinzel",serif;font-size:7px;display:flex;align-items:center;justify-content:center}
.review .thumb{width:67px;height:59px;position:absolute;left:0;top:0}
.review-text{position:absolute;left:88px;top:6px;width:150px;font-size:7.5px;color:var(--review-text);line-height:16px}
.stars{position:absolute;left:88px;top:40px}

/* footer */
.site-footer{left:0;top:1145px;width:793px;height:55px;background:var(--gold)}
.footer-nav{left:86px;top:13px;font-family:"Cinzel",serif;font-size:8.5px;color:var(--footer-text);white-space:nowrap;word-spacing:2px}
.copyright{left:88px;top:33px;font-family:"Cinzel",serif;font-size:8px;color:var(--footer-text)}
.social{top:18px;width:22px;height:22px;border-radius:50%;background:#111;color:var(--gold);font-size:6px;display:flex;align-items:center;justify-content:center}
</style>
</head>
<body>

<header class="abs site-header">
  <div class="abs brand"><span class="brand-name">VANTAGE</span><span class="brand-sub">MUSIC PRODUCTIONS</span></div>
  <svg class="abs nav-note" width="8" height="14" viewBox="0 0 8 14"><circle cx="3" cy="11" r="2.5" fill="#c8a75a"/><path d="M5 11 V1 L8 3" stroke="#c8a75a" stroke-width="1.2" fill="none"/></svg>
  <nav class="main-nav">
    <a href="#" style="left:316px">Home</a>
    <a href="#" style="left:368px">About Us</a>
    <a href="#" style="left:431px">Create a Profile</a>
    <a href="#" style="left:540px">Music Producers</a>
    <a href="#" style="left:651px">Contct Us</a>
  </nav>
  <div class="abs account-btn signup">SIGN UP</div>
  <div class="abs account-btn login">LOGIN</div>
</header>

<section class="abs hero" role="img" aria-label="Recording studio mixing console with monitor speakers and wood paneling"></section>
<p class="abs hero-tagline">We Turn Aspiring Musicians Into SuperStars!</p>
<h2 class="abs form-title">Submit Music Demo</h2>
<form class="abs demo-form">
  <div class="field" style="top:10px">First Name</div>
  <div class="field" style="top:37px">Last Name</div>
  <div class="field" style="top:62px">E-Mail</div>
  <div class="field" style="top:88px;width:47px">Age</div>
  <div class="field" style="top:88px;left:65px;width:108px">Zip- Code</div>
  <div class="field" style="top:114px">Daytime Phone</div>
  <div class="field" style="top:139px">Evening Phone</div>
  <div class="field comments" style="top:167px">Comments</div>
  <div class="submit-btn">SUBMIT</div>
</form>
<div class="abs slider-track"></div>
<div class="abs slider-thumb"></div>

<section class="abs partners">
  <span class="partner">Northwave</span>
  <span class="partner">Fightline</span>
  <span class="partner">Tunecast</span>
  <span class="partner">Homebox</span>
  <span class="partner">Arcadia</span>
  <span class="partner">Crewline</span>
  <span class="partner">Ironhall</span>
</section>

<svg width="0" height="0" style="position:absolute">
  <defs>
    <symbol id="play" viewBox="0 0 26 26"><circle cx="13" cy="13" r="12" fill="#1b1b1b" fill-opacity=".7" stroke="#fff" stroke-width="1.5"/><path d="M10 8 L19 13 L10 18 Z" fill="#fff"/></symbol>
    <symbol id="star" viewBox="0 0 20 20"><path d="M10 1 L12.6 7.2 L19.3 7.7 L14.2 12 L15.8 18.6 L10 15 L4.2 18.6 L5.8 12 L0.7 7.7 L7.4 7.2 Z" fill="#c9a54e"/></symbol>
  </defs>
</svg>

<h2 class="abs section-title" style="left:80px;top:483px">Latest Uploaded Music Demos</h2>
<div class="abs arrow-btn" style="left:394px"><svg width="8" height="8"><path d="M7 0 L1 4 L7 8 Z" fill="#000"/></svg></div>
<div class="abs arrow-btn" style="left:414px"><svg width="8" height="8"><path d="M1 0 L7 4 L1 8 Z" fill="#000"/></svg></div>

<div class="abs demo-card" style="left:85px;top:516px"><div class="thumb" role="img" aria-label="Rock singer performing on a blue-lit stage" style="background:radial-gradient(circle at 30% 20%,#4fb0c8 0%,transparent 40%),radial-gradient(circle at 60% 60%,#2a2a30 0%,transparent 50%),linear-gradient(135deg,#1d5a6e,#0d1b26 70%,#6a1a1a)"><svg class="play"><use href="#play"/></svg></div><p class="caption">Name : Dana Wilde<br>Song : I will also be<br>Time : 1.45</p></div>
<div class="abs demo-card" style="left:205px;top:518px"><div class="thumb" role="img" aria-label="Female pop singer with microphone" style="background:radial-gradient(ellipse at 45% 35%,#f0c890 0%,#c98a5c 25%,transparent 55%),linear-gradient(135deg,#8a3a9a,#3a1a5a 60%,#c98a7a)"><svg class="play"><use href="#play"/></svg></div><p class="caption">Name : Dana Wilde<br>Song : I will also be<br>Time : 1.45</p></div>
<div class="abs demo-card" style="left:323px;top:518px"><div class="thumb" role="img" aria-label="Singer with platinum hair on stage" style="background:radial-gradient(ellipse at 65% 30%,#f0f0f5 0%,#9a9aa5 20%,transparent 45%),radial-gradient(circle at 40% 70%,#3a3a3a,transparent 50%),#070707"><svg class="play"><use href="#play"/></svg></div><p class="caption">Name : Dana Wilde<br>Song : I will also be<br>Time : 1.45</p></div>

<div class="abs demo-card" style="left:85px;top:665px"><div class="thumb" role="img" aria-label="Hip hop artist in sunglasses with microphone" style="background:radial-gradient(circle at 15% 30%,#3a7ae0 0%,transparent 35%),radial-gradient(ellipse at 65% 50%,#b07a4a 0%,#6a4022 30%,transparent 60%),linear-gradient(135deg,#1a2a5a,#2a1a10)"><svg class="play"><use href="#play"/></svg></div><p class="caption">Name : Dana Wilde<br>Song : I will also be<br>Time : 1.45</p></div>
<div class="abs demo-card" style="left:205px;top:665px"><div class="thumb" role="img" aria-label="Black and white photo of a rock vocalist" style="background:radial-gradient(ellipse at 75% 35%,#cfcfcf 0%,#7a7a7a 25%,transparent 55%),radial-gradient(circle at 25% 60%,#9a9a9a,transparent 35%),linear-gradient(135deg,#4a4a4a,#0a0a0a)"><svg class="play"><use href="#play"/></svg></div><p class="caption">Name : Dana Wilde<br>Song : I will also be<br>Time : 1.45</p></div>
<div class="abs demo-card" style="left:323px;top:665px"><div class="thumb" role="img" aria-label="Female singer under warm stage lights" style="background:radial-gradient(circle at 85% 20%,#f5e0b0 0%,#c9904a 20%,transparent 45%),radial-gradient(ellipse at 40% 45%,#a0704a 0%,transparent 40%),linear-gradient(135deg,#3a2414,#0a0604)"><svg class="play"><use href="#play"/></svg></div><p class="caption">Name : Dana Wilde<br>Song : I will also be<br>Time : 1.45</p></div>

<div class="abs demo-card" style="left:85px;top:809px"><div class="thumb" role="img" aria-label="Red-haired rock singer pointing to the crowd" style="background:radial-gradient(ellipse at 30% 25%,#e04a1a 0%,transparent 35%),radial-gradient(ellipse at 40% 75%,#f08a2a 0%,transparent 40%),linear-gradient(135deg,#4a8ac0,#2a4a7a)"><svg class="play"><use href="#play"/></svg></div><p class="caption">Name : Dana Wilde<br>Song : I will also be<br>Time : 1.45</p></div>
<div class="abs demo-card" style="left:205px;top:809px"><div class="thumb" role="img" aria-label="Blonde singer performing on blue stage" style="background:radial-gradient(ellipse at 60% 30%,#f5d8a0 0%,#c9a06a 25%,transparent 50%),radial-gradient(circle at 50% 80%,#3a8a7a,transparent 40%),linear-gradient(135deg,#1a3a8a,#0a1030)"><svg class="play"><use href="#play"/></svg></div><p class="caption">Name : Dana Wilde<br>Song : I will also be<br>Time : 1.45</p></div>
<div class="abs demo-card" style="left:323px;top:809px"><div class="thumb" role="img" aria-label="Masked metal performer in amber light" style="background:radial-gradient(circle at 20% 20%,#f0a040 0%,#a0501a 30%,transparent 60%),radial-gradient(ellipse at 80% 40%,#c0c0c0 0%,transparent 25%),linear-gradient(135deg,#5a2a0a,#080402)"><svg class="play"><use href="#play"/></svg></div><p class="caption">Name : Dana Wilde<br>Song : I will also be<br>Time : 1.45</p></div>

<div class="abs demo-card" style="left:85px;top:964px"><div class="thumb" role="img" aria-label="Acoustic musician seated in a room" style="background:radial-gradient(ellipse at 30% 20%,#b0a090 0%,transparent 40%),radial-gradient(ellipse at 60% 55%,#8a6a4a 0%,transparent 40%),linear-gradient(135deg,#5a4a3a,#1e1812)"><svg class="play"><use href="#play"/></svg></div><p class="caption">Name : Dana Wilde<br>Song : I will also be<br>Time : 1.45</p></div>
<div class="abs demo-card" style="left:205px;top:964px"><div class="thumb" role="img" aria-label="Singer under bright pink and violet lights" style="background:radial-gradient(ellipse at 70% 40%,#f8c0f0 0%,#e060d0 25%,transparent 55%),radial-gradient(circle at 20% 80%,#ff40c0,transparent 40%),linear-gradient(135deg,#3a2ad0,#8a1aa0)"><svg class="play"><use href="#play"/></svg></div><p class="caption">Name : Dana Wilde<br>Song : I will also be<br>Time : 1.45</p></div>
<div class="abs demo-card" style="left:323px;top:964px"><div class="thumb" role="img" aria-label="Moody portrait of a vocalist in shadow" style="background:radial-gradient(ellipse at 70% 30%,#8a8a8a 0%,#3a3a3a 25%,transparent 50%),linear-gradient(135deg,#2a2a2a,#030303)"><svg class="play"><use href="#play"/></svg></div><p class="caption">Name : Dana Wilde<br>Song : I will also be<br>Time : 1.45</p></div>

<nav class="abs pager">
  <span class="page wide">Prev</span><span class="page">1</span><span class="page">2</span><span class="page">3</span><span class="page">4</span><span class="page">5</span><span class="page">6</span><span class="page">...</span><span class="page">22</span><span class="page wide">Next</span>
</nav>

<h2 class="abs section-title" style="left:472px;top:483px">List of Selected Musics</h2>
<article class="abs track" style="top:518px"><div class="thumb" role="img" aria-label="Artist performing under red light" style="background:radial-gradient(ellipse at 40% 35%,#d0a080 0%,transparent 35%),linear-gradient(135deg,#c03a1a,#3a0a06)"><svg class="play"><use href="#play"/></svg></div><h3 class="track-title">Neque porro quisquam est qui</h3><p class="track-text">Lorem Ipsum is simply dummy text of the printing and typesetting industry.</p></article>
<article class="abs track" style="top:603px"><div class="thumb" role="img" aria-label="Singer with guitar in golden light" style="background:radial-gradient(ellipse at 30% 30%,#e06a3a 0%,transparent 35%),linear-gradient(135deg,#c9a04a,#5a4010)"><svg class="play"><use href="#play"/></svg></div><h3 class="track-title">Neque porro quisquam est qui</h3><p class="track-text">Lorem Ipsum is simply dummy text of the printing and typesetting industry.</p></article>
<article class="abs track" style="top:688px"><div class="thumb" role="img" aria-label="Female vocalist on dark red stage" style="background:radial-gradient(ellipse at 45% 40%,#c09080 0%,transparent 35%),linear-gradient(135deg,#9a2a2a,#0a0a0a)"><svg class="play"><use href="#play"/></svg></div><h3 class="track-title">Neque porro quisquam est qui</h3><p class="track-text">Lorem Ipsum is simply dummy text of the printing and typesetting industry.</p></article>
<div class="abs read-more" style="left:649px;top:769px">READ MORE</div>

<h2 class="abs section-title" style="left:473px;top:822px">Latest  Reviews</h2>
<article class="abs track review" style="left:472px;top:856px"><div class="thumb" role="img" aria-label="Young singer performing live" style="background:radial-gradient(ellipse at 60% 40%,#e8c890 0%,transparent 40%),linear-gradient(135deg,#2a2a3a,#8a8a90)"></div><p class="review-text">Sed ut perspiciatis unde omnis iste natus error sit voluptatem accusantium</p><svg class="stars" width="96" height="16"><use href="#star" x="0" width="16" height="16"/><use href="#star" x="19" width="16" height="16"/><use href="#star" x="38" width="16" height="16"/><use href="#star" x="57" width="16" height="16"/><use href="#star" x="76" width="16" height="16"/></svg></article>
<article class="abs track review" style="left:472px;top:945px"><div class="thumb" role="img" aria-label="Blonde singer close-up with red backdrop" style="background:radial-gradient(ellipse at 55% 45%,#f0d0a0 0%,#d09060 30%,transparent 60%),linear-gradient(135deg,#c02a1a,#6a1008)"></div><p class="review-text">Sed ut perspiciatis unde omnis iste natus error sit voluptatem accusantium</p><svg class="stars" width="96" height="16"><use href="#star" x="0" width="16" height="16"/><use href="#star" x="19" width="16" height="16"/><use href="#star" x="38" width="16" height="16"/><use href="#star" x="57" width="16" height="16"/><use href="#star" x="76" width="16" height="16"/></svg></article>
<article class="abs track review" style="left:472px;top:1025px"><div class="thumb" role="img" aria-label="Pop singer on red-lit stage" style="background:radial-gradient(ellipse at 50% 40%,#b07a6a 0%,transparent 35%),linear-gradient(135deg,#d03a3a,#2a0a0a)"></div><p class="review-text">Sed ut perspiciatis unde omnis iste natus error sit voluptatem accusantium</p><svg class="stars" width="96" height="16"><use href="#star" x="0" width="16" height="16"/><use href="#star" x="19" width="16" height="16"/><use href="#star" x="38" width="16" height="16"/><use href="#star" x="57" width="16" height="16"/><use href="#star" x="76" width="16" height="16"/></svg></article>
<div class="abs read-more" style="left:649px;top:1102px">READ MORE</div>

<footer class="abs site-footer">
  <p class="abs footer-nav">Home &nbsp;|&nbsp; About Us &nbsp;|&nbsp; Create a Profile &nbsp;|&nbsp; Music Producers &nbsp;|&nbsp; Contact Us</p>
  <p class="abs copyright">Copyright ©2013 &nbsp;Company Name &nbsp;&nbsp;- All Rights Reserved</p>
  <span class="abs social" style="left:635px">Share</span>
  <span class="abs social" style="left:660px">Like</span>
  <span class="abs social" style="left:685px">Post</span>
</footer>

</body>
</html>
```